Business Card Design - Amberfield Court

We are looking at a new design for our business cards that has a modern and professional look. We run a residential aged care facility focussing on the care of residents. The cards will be used for potential clients, consultants and business opportunities in this sector. Blue and white is our main colours and would to see these colours incorporated in the design.
Industry/Entity Type
Business
Contact Information for Business Card
Amberfield Court, Darren Walsh, dwalsh@amberfieldcourt.com.au, Finance Manager, 0472 639 208, BCom, 37 Marrabel Crescent, Brindle Vale, Qld 4093.
Look and feel
Each slider illustrates characteristics of the customer's brand and the style your logo design should communicate.

```html
<!DOCTYPE html>
<html lang="en">
<head>
<meta charset="utf-8">
<title>Amberfield Court – Business Card</title>
<link rel="stylesheet" href="https://fonts.googleapis.com/css2?family=Open+Sans:wght@400;600;700&display=swap">
<style>
  :root {
    --navy: #1e3b4b;
    --steel: #4a7d9c;
    --white: #ffffff;
    --stage: #2e2f31;
    --shadow: rgba(0,0,0,0.35);
  }
  * { margin: 0; padding: 0; box-sizing: border-box; }
  html, body {
    width: 1200px; height: 900px; overflow: hidden;
    background: var(--stage);
    font-family: "Open Sans", Arial, sans-serif;
  }
  .canvas { position: relative; width: 1200px; height: 900px; }
  .card {
    position: absolute; width: 720px; height: 400px;
    border-radius: 26px; overflow: hidden;
    box-shadow: 0 14px 30px var(--shadow);
    background: var(--white);
  }
  .card-front { left: 110px; top: 40px; }
  .card-back { left: 370px; top: 470px; }

  /* front */
  .front-brand {
    position: absolute; inset: 0;
    display: flex; align-items: center; justify-content: center; gap: 22px;
  }
  .brand-dot {
    width: 64px; height: 64px; border-radius: 50%;
    background: var(--navy); flex: none;
  }
  .brand-name {
    font-weight: 600; font-size: 40px; letter-spacing: 3px;
    text-transform: uppercase; color: var(--navy);
  }

  /* back */
  .back-shapes { position: absolute; inset: 0; width: 100%; height: 100%; }
  .contact {
    position: absolute; left: 60px; top: 148px; color: var(--white);
  }
  .contact-name { font-weight: 700; font-size: 32px; line-height: 1.05; text-transform: uppercase; }
  .contact-role { font-size: 14px; text-transform: uppercase; margin-bottom: 16px; }
  .contact-line { display: flex; align-items: center; gap: 10px; font-size: 16px; line-height: 1.5; }
  .contact-line svg { width: 14px; height: 14px; fill: var(--white); flex: none; }
  .contact-address { font-size: 16px; line-height: 1.35; margin-top: 12px; padding-left: 24px; }
  .back-brand {
    position: absolute; right: 34px; top: 205px;
    display: flex; align-items: center; gap: 10px;
  }
  .back-brand .brand-dot { width: 34px; height: 34px; background: var(--steel); }
  .back-brand .brand-name {
    font-size: 19px; letter-spacing: 2px; line-height: 1.15; color: var(--steel);
  }
</style>
</head>
<body>
<main class="canvas">

  <section class="card card-front" aria-label="Card front">
    <div class="front-brand">
      <span class="brand-dot"></span>
      <span class="brand-name">Amberfield Court</span>
    </div>
  </section>

  <section class="card card-back" aria-label="Card back">
    <svg class="back-shapes" viewBox="0 0 720 400" preserveAspectRatio="none" aria-hidden="true">
      <path fill="var(--steel)" d="M0,0 H720 V82 C610,95 520,125 495,200 C470,285 440,345 310,358 C200,368 80,352 0,342 Z"/>
      <path fill="var(--navy)" d="M0,0 H720 V58 C600,74 505,108 478,188 C452,270 425,325 305,338 C195,348 80,335 0,322 Z"/>
      <path fill="var(--steel)" d="M0,372 C110,385 220,392 330,400 H0 Z"/>
    </svg>

    <div class="contact">
      <h1 class="contact-name">Darren Walsh</h1>
      <p class="contact-role">Finance Manager (BCom)</p>
      <p class="contact-line">
        <svg viewBox="0 0 24 24"><path d="M6.6 10.8a15.1 15.1 0 0 0 6.6 6.6l2.2-2.2a1 1 0 0 1 1-.25 11.4 11.4 0 0 0 3.6.57 1 1 0 0 1 1 1V20a1 1 0 0 1-1 1A17 17 0 0 1 3 4a1 1 0 0 1 1-1h3.5a1 1 0 0 1 1 1c0 1.25.2 2.45.57 3.57a1 1 0 0 1-.25 1z"/></svg>
        0472 639 208
      </p>
      <p class="contact-line">
        <svg viewBox="0 0 24 24"><path d="M3 5h18v14H3zm2 2v.5l7 4.5 7-4.5V7zm0 2.9V17h14V9.9l-7 4.5z"/></svg>
        dwalsh@amberfieldcourt.com.au
      </p>
      <p class="contact-address">37 Marrabel Crescent<br>Brindle Vale, Qld 4093</p>
    </div>

    <div class="back-brand">
      <span class="brand-dot"></span>
      <span class="brand-name">Amberfield<br>Court</span>
    </div>
  </section>

</main>
</body>
</html>
```